Business Card Design for Software Development Company

I am looking for a business card design the incorporates my new logo (attached below).

Key information to include:
Name: Martin Quelbrook
Title: CEO
Email: martin@brightwellcivic.example
Phone: 555-218-9403
Website: www.brightwellcivic.example

NOTE: This design should be easy to edit so that we can order cards for different members of our team.

```html
<!DOCTYPE html>
<html lang="en">
<head>
<meta charset="utf-8">
<title>Brightwell Labs – Business Card</title>
<link rel="stylesheet" href="https://fonts.googleapis.com/css2?family=Montserrat:wght@400;500;700;800&display=swap">
<style>
  :root {
    --bg: #3a3a3c;
    --lavender: #6f799d;
    --lavender-deep: #5d6789;
    --navy: #333a52;
    --orange: #ec7c26;
    --white: #ffffff;
    --ink: #2b2f3d;
  }
  * { box-sizing: border-box; margin: 0; padding: 0; }
  html, body { width: 1200px; height: 1200px; overflow: hidden; }
  body {
    background: var(--bg);
    font-family: "Montserrat", sans-serif;
    position: relative;
  }
  .card {
    position: absolute;
    left: 150px;
    width: 900px;
    height: 514px;
    border-radius: 34px;
    overflow: hidden;
  }
  .card-back {
    top: 56px;
    background: var(--lavender);
    display: flex;
    align-items: center;
    justify-content: center;
  }
  .card-back .wordmark {
    font-weight: 800;
    font-size: 84px;
    letter-spacing: -2px;
    color: var(--lavender-deep);
  }
  .card-front {
    top: 630px;
    background: var(--white);
  }
  .front-bg {
    position: absolute;
    inset: 0;
    width: 100%;
    height: 100%;
  }
  .front-wordmark {
    position: absolute;
    left: 120px;
    top: 46px;
    font-weight: 800;
    font-size: 90px;
    letter-spacing: -3px;
    color: var(--navy);
    line-height: 1;
    white-space: nowrap;
  }
  .identity {
    position: absolute;
    left: 120px;
    top: 176px;
    width: 330px;
    text-align: right;
  }
  .identity .name {
    font-weight: 700;
    font-size: 34px;
    color: var(--orange);
    white-space: nowrap;
  }
  .identity .title {
    font-weight: 500;
    font-size: 20px;
    color: var(--ink);
    margin-top: 4px;
  }
  .divider {
    position: absolute;
    left: 470px;
    top: 166px;
    width: 2px;
    height: 104px;
    background: var(--orange);
  }
  .contacts {
    position: absolute;
    left: 494px;
    top: 166px;
    list-style: none;
  }
  .contacts li {
    display: flex;
    align-items: center;
    gap: 12px;
    font-size: 19px;
    font-weight: 400;
    color: var(--ink);
    height: 35px;
    white-space: nowrap;
  }
  .contacts svg { width: 18px; height: 18px; flex: none; }
</style>
</head>
<body>

  <section class="card card-back" aria-label="Card back">
    <span class="wordmark">Brightwell Labs</span>
  </section>

  <section class="card card-front" aria-label="Card front">
    <svg class="front-bg" viewBox="0 0 900 514" preserveAspectRatio="none" aria-hidden="true">
      <path d="M0 445 Q 560 415 900 305 L900 514 L0 514 Z" fill="var(--lavender)"/>
      <path d="M200 424 Q 580 388 885 290 Q 590 400 200 426 Z" fill="var(--orange)"/>
    </svg>

    <div class="front-wordmark">Brightwell Labs</div>

    <div class="identity">
      <div class="name">Martin Quelbrook</div>
      <div class="title">CEO</div>
    </div>

    <div class="divider"></div>

    <ul class="contacts">
      <li>
        <svg viewBox="0 0 24 24"><path fill="var(--orange)" d="M6.6 10.8a15.2 15.2 0 0 0 6.6 6.6l2.2-2.2c.3-.3.7-.4 1-.2 1.1.4 2.3.6 3.6.6.6 0 1 .4 1 1V20c0 .6-.4 1-1 1A17 17 0 0 1 3 4c0-.6.4-1 1-1h3.5c.6 0 1 .4 1 1 0 1.3.2 2.5.6 3.6.1.3 0 .7-.2 1z"/></svg>
        555-218-9403
      </li>
      <li>
        <svg viewBox="0 0 24 24"><path fill="var(--orange)" d="M2 5h20v14H2z"/><path fill="none" stroke="#fff" stroke-width="1.8" d="M2.5 5.5 12 13l9.5-7.5"/></svg>
        martin@brightwellcivic.example
      </li>
      <li>
        <svg viewBox="0 0 24 24"><circle cx="12" cy="12" r="10" fill="var(--orange)"/><path fill="none" stroke="#fff" stroke-width="1.4" d="M2 12h20M12 2c3 3 3 17 0 20M12 2c-3 3-3 17 0 20"/></svg>
        www.brightwellcivic.example
      </li>
    </ul>
  </section>

</body>
</html>
```